Looking for someone to design a business card for my plumbing business Quandor Plumbing Solutions I want the background also to be black, must attract clients. If possible I want the front to be the logo and the back to show maybe the details.

Target Market(s)

Clients

Industry/Entity Type

Plumbing maintenance

Contact Information for Business Card

Name: Felix, Contact: 0461 539 207, Email: quandorplumbingsolutions@mailbrook.example, Licence number 728093K

Font styles to use
Other font styles liked:
• as per logo maybe?

Colors

Designer to choose colors to be used in the design.

Requirements
Nice to have
• stating the service I provide, emergency plumbing, plumbing maintenance, drainage maintenance, block sewer and stormwater, camera and locating.

```html
<!DOCTYPE html>
<html lang="en">
<head>
<meta charset="utf-8">
<title>Quandor Plumbing Solutions – Business Card</title>
<link href="https://fonts.googleapis.com/css2?family=Montserrat:wght@400;500;700;800&display=swap" rel="stylesheet">
<style>
  :root {
    --backdrop: #e4e4e4;
    --card: #202020;
    --card-edge: #4a8fd8;
    --accent: #4a8fd8;
    --text: #f2f2f2;
    --text-dim: #cfcfcf;
    --emboss: #3a3a3a;
  }
  * { box-sizing: border-box; margin: 0; padding: 0; }
  html, body {
    width: 1200px; height: 801px; overflow: hidden;
    background: var(--backdrop);
    font-family: "Montserrat", sans-serif;
  }
  .sheet {
    position: relative; width: 1200px; height: 801px;
  }
  .card {
    position: absolute; top: 237px;
    width: 540px; height: 327px;
    background: var(--card);
    border-bottom: 4px solid var(--card-edge);
    box-shadow: 0 10px 24px rgba(0,0,0,.18);
    overflow: hidden;
  }
  .card--details { left: 40px; }
  .card--brand { left: 620px; }

  /* details side */
  .brand-lockup {
    position: absolute; left: 24px; top: 80px; width: 176px;
    display: flex; align-items: center; gap: 10px;
  }
  .brand-lockup__dot {
    flex: none; width: 16px; height: 16px; border-radius: 50%;
    background: var(--accent);
  }
  .brand-lockup__name {
    color: var(--text); font-weight: 800; font-size: 17px;
    line-height: 1.15; text-transform: uppercase; letter-spacing: .5px;
  }
  .divider {
    position: absolute; left: 215px; top: 40px;
    width: 1.5px; height: 150px; background: var(--accent);
  }
  .contact {
    position: absolute; left: 235px; top: 42px; right: 16px;
    color: var(--text);
  }
  .contact__name {
    color: var(--accent); font-weight: 800; font-size: 22px;
    letter-spacing: .5px; line-height: 1;
  }
  .contact__role { font-size: 12.5px; margin-top: 4px; }
  .contact__licence { font-size: 12.5px; margin-top: 10px; }
  .contact__list { list-style: none; margin-top: 10px; }
  .contact__item {
    display: flex; align-items: center; gap: 7px;
    font-size: 10.5px; line-height: 1.9; white-space: nowrap;
  }
  .contact__item--phone { font-size: 12.5px; }
  .contact__icon { flex: none; width: 11px; height: 11px; }
  .contact__icon--circle {
    border-radius: 50%; background: var(--accent);
  }
  .services {
    position: absolute; left: 24px; right: 24px; bottom: 30px;
    color: var(--text); font-size: 12px; line-height: 1.75;
    text-align: center;
  }
  .services__sep { color: var(--accent); margin: 0 6px; }

  /* brand side */
  .brand-mark {
    position: absolute; inset: 0;
    display: flex; align-items: center; justify-content: center;
    gap: 16px;
  }
  .brand-mark__dot {
    width: 34px; height: 34px; border-radius: 50%; background: var(--emboss);
  }
  .brand-mark__name {
    color: var(--emboss); font-weight: 800; font-size: 30px;
    line-height: 1.05; text-transform: uppercase; letter-spacing: 1px;
  }
</style>
</head>
<body>
<main class="sheet">
  <section class="card card--details" aria-label="Business card, details side">
    <div class="brand-lockup">
      <span class="brand-lockup__dot"></span>
      <span class="brand-lockup__name">Quandor Plumbing Solutions</span>
    </div>
    <div class="divider"></div>
    <div class="contact">
      <p class="contact__name">FELIX</p>
      <p class="contact__role">Founder &amp; CEO</p>
      <p class="contact__licence">Licence number 728093K</p>
      <ul class="contact__list">
        <li class="contact__item contact__item--phone">
          <svg class="contact__icon" viewBox="0 0 24 24" aria-hidden="true"><path fill="#4a8fd8" d="M6.6 10.8a15.1 15.1 0 0 0 6.6 6.6l2.2-2.2c.3-.3.7-.4 1-.2 1.1.4 2.3.6 3.6.6.6 0 1 .4 1 1V20c0 .6-.4 1-1 1A17 17 0 0 1 3 4c0-.6.4-1 1-1h3.5c.6 0 1 .4 1 1 0 1.3.2 2.5.6 3.6.1.3 0 .7-.2 1z"/></svg>
          0461 539 207
        </li>
        <li class="contact__item">
          <svg class="contact__icon" viewBox="0 0 24 24" aria-hidden="true"><rect x="2" y="5" width="20" height="14" fill="#4a8fd8"/><path d="M2 5l10 8 10-8" fill="none" stroke="#202020" stroke-width="2"/></svg>
          quandorplumbingsolutions@mailbrook.example
        </li>
        <li class="contact__item">
          <span class="contact__icon contact__icon--circle"></span>
          @QuandorPlumbingSolutions
        </li>
      </ul>
    </div>
    <p class="services">
      Emergency plumbing<span class="services__sep">•</span>Plumbing maintenance<span class="services__sep">•</span>Drainage maintenance<br>
      Block sewer and stormwater<span class="services__sep">•</span>Camera and locating
    </p>
  </section>

  <section class="card card--brand" aria-label="Business card, brand side">
    <div class="brand-mark">
      <span class="brand-mark__dot"></span>
      <span class="brand-mark__name">Quandor<br>Plumbing Solutions</span>
    </div>
  </section>
</main>
</body>
</html>
```